Sports / Entertainment Media Co needs a biz card design

We are a media co / luxury lifestyle brand that targets professional athletes, entertainers and high net-worth fans. We are currently preparing for a relaunch and in need for new biz cards. I envision a black on black card with a pop of color on opposite side. Color Palette black, white, red etc. I want this card to exude sexiness and power. Very high stylized, hip and cool. I have attached the logo - I would like to see it all in black, but also open to other ideas. I will also upload a current card with all information needed on this new card. Furthermore I will add some samples of other cards I love. Thanks!!!
Updates

I provided suggestions, however I am open to all ideas!!   Be as creative as you can.  Think cutting-edge, sexy and powerful.  Take a look at the cards I uploaded to get a sense for what I like.  Thanks!!!

Industry/Entity Type

Entertainment

```html
<!DOCTYPE html>
<html lang="en">
<head>
<meta charset="utf-8">
<title>Vaulto — Business Card</title>
<link href="https://fonts.googleapis.com/css2?family=Exo+2:wght@400;500;800&display=swap" rel="stylesheet">
<style>
  :root {
    --stage: #2b2b2b;
    --ink: #111111;
    --paper: #ffffff;
    --paper-shade: #e4e4e4;
    --accent: #ff1a1a;
    --muted: #8a8a8a;
    --bar: #0d0d0d;
  }
  * { box-sizing: border-box; margin: 0; padding: 0; }
  html, body { width: 1200px; height: 892px; overflow: hidden; }
  body {
    background: var(--stage);
    font-family: "Exo 2", sans-serif;
    display: flex;
    flex-direction: column;
    align-items: center;
    justify-content: center;
    gap: 56px;
  }
  .card {
    position: relative;
    width: 620px;
    height: 354px;
    background: radial-gradient(ellipse at 55% 45%, var(--paper) 0%, var(--paper) 40%, var(--paper-shade) 100%);
    overflow: hidden;
  }

  /* wordmark */
  .wordmark {
    display: flex;
    align-items: center;
    gap: 8px;
  }
  .wordmark-name {
    font-weight: 800;
    color: var(--ink);
    letter-spacing: -1px;
    line-height: 1;
  }
  .wordmark-dot {
    border-radius: 50%;
    background: var(--accent);
  }
  .wordmark-tag {
    font-size: 9px;
    color: var(--muted);
    letter-spacing: 0.5px;
    text-align: right;
  }

  /* back side */
  .card-back .web-band {
    position: absolute;
    left: 0; right: 0; bottom: 0;
    height: 58px;
    background: var(--ink);
    display: flex;
    align-items: center;
    padding-left: 28px;
    color: var(--paper);
    font-size: 15px;
    letter-spacing: 1px;
  }
  .card-back .logo-block {
    position: absolute;
    left: 50%; top: 42%;
    transform: translate(-50%, -50%);
  }
  .card-back .wordmark-name { font-size: 66px; }
  .card-back .wordmark-dot { width: 18px; height: 18px; }

  /* front side */
  .card-front .logo-block {
    position: absolute;
    right: 34px; top: 26px;
  }
  .card-front .wordmark-name { font-size: 58px; }
  .card-front .wordmark-dot { width: 16px; height: 16px; }

  .name-plate {
    position: absolute;
    left: 28px; top: 112px;
    width: 300px; height: 70px;
    background: var(--accent);
    border-radius: 8px;
    color: var(--paper);
    padding: 12px 18px;
  }
  .name-plate .person {
    font-size: 24px;
    font-weight: 500;
    letter-spacing: 1.5px;
    line-height: 1.1;
  }
  .name-plate .role {
    font-size: 11px;
    letter-spacing: 2px;
    margin-top: 3px;
  }

  .contact-list {
    position: absolute;
    left: 28px; top: 194px;
    width: 300px;
    list-style: none;
    display: flex;
    flex-direction: column;
    gap: 9px;
  }
  .contact-item {
    height: 44px;
    background: var(--bar);
    border-radius: 7px;
    display: flex;
    align-items: center;
    gap: 14px;
    padding: 0 14px;
    color: var(--paper);
    font-size: 12.5px;
    letter-spacing: 0.8px;
    line-height: 1.3;
  }
  .contact-icon {
    flex: 0 0 24px;
    width: 24px; height: 24px;
    border-radius: 4px;
    background: #2a2a2a;
    display: flex; align-items: center; justify-content: center;
  }
  .contact-icon svg { width: 15px; height: 15px; fill: var(--paper); }
</style>
</head>
<body>

  <section class="card card-back" aria-label="Card back">
    <div class="logo-block">
      <div class="wordmark">
        <span class="wordmark-name">vaulto</span>
        <span class="wordmark-dot"></span>
      </div>
      <div class="wordmark-tag">vaultomedia.com</div>
    </div>
    <div class="web-band">www.vaultomedia.com</div>
  </section>

  <section class="card card-front" aria-label="Card front">
    <div class="logo-block">
      <div class="wordmark">
        <span class="wordmark-name">vaulto</span>
        <span class="wordmark-dot"></span>
      </div>
      <div class="wordmark-tag">vaultomedia.com</div>
    </div>

    <div class="name-plate">
      <div class="person">MARK HALDEN</div>
      <div class="role">GENERAL MANAGER</div>
    </div>

    <ul class="contact-list">
      <li class="contact-item">
        <span class="contact-icon">
          <svg viewBox="0 0 16 16" aria-hidden="true"><path d="M8 1.5 1 7.5h2V14h4v-4h2v4h4V7.5h2z"/></svg>
        </span>
        <span>42 Arden Lane,<br>Suite 7 West</span>
      </li>
      <li class="contact-item">
        <span class="contact-icon">
          <svg viewBox="0 0 16 16" aria-hidden="true"><path d="M2 5c0-1.5 2.5-3 6-3s6 1.5 6 3v1.5h-3.5V5h-5v1.5H2zM4 8h8l1.5 5h-11z"/></svg>
        </span>
        <span>012 555 0147<br>012 555 0198</span>
      </li>
      <li class="contact-item">
        <span class="contact-icon">
          <svg viewBox="0 0 16 16" aria-hidden="true"><path d="M3 2h10v12H3zM4.5 3.5v9h7v-9z"/></svg>
        </span>
        <span>mark@vaultomedia.com<br>www.vaultomedia.com</span>
      </li>
    </ul>
  </section>

</body>
</html>
```